I have a website called Okenta Holdings (okentaholdings.com) that I would like to have redesigned. Most of the content is already created, but I need a new design. You can also see my other website at brambleacres.com. I am open to a new logo or modifying the current logo if you have a good idea. Please feel free to use other images for the home page (and maybe some other locations) if you feel they provide a better look and feel to the website. I prefer a modern look.

Important: You do not have to use the images I've provided for the home page. Feel free to find your own stock photos. You don't have to pay for them unless I select your design.

1) Please use wix.com to make your changes so that I can edit it later.
2) I will need all the graphics files to be saved so I can dowload it for later.
3) I will be adding more content to the site later.
4) This site will likely be transferred over to brambleacres.com so if you make a logo please make one for Okenta Holdings and one for Bramble Acres.
5) You can use other images that you feel would help the look and feel of the website.

```html
<!DOCTYPE html>
<html lang="en">
<head>
<meta charset="utf-8">
<title>Okenta Holdings</title>
<link href="https://fonts.googleapis.com/css2?family=Oswald:wght@500;600&family=Roboto:wght@400;500;700&display=swap" rel="stylesheet">
<style>
:root{
  --navy:#2b4a6c;
  --footer:#294a6b;
  --accent:#4b8fd0;
  --accent-dark:#3a6ea5;
  --text:#6f6f6f;
  --ink:#1e2a36;
  --white:#ffffff;
}
*{margin:0;padding:0;box-sizing:border-box}
html,body{width:1200px;height:3183px;overflow:hidden;background:var(--white)}
body{position:relative;font-family:'Roboto',sans-serif;color:var(--ink)}
.abs{position:absolute}
.btn{position:absolute;background:var(--accent);color:var(--white);font:700 15px 'Roboto',sans-serif;display:flex;align-items:center;justify-content:center;text-transform:uppercase}
.heading{font-family:'Oswald',sans-serif;font-weight:600;text-transform:uppercase;color:var(--navy);white-space:nowrap}

/* hero */
.hero{left:0;top:0;width:1200px;height:651px;background:linear-gradient(180deg,#c9c3d6 0%,#d9a98e 30%,#e3a56a 45%,#8a8ea6 62%,#5d6f86 78%,#3f5a3e 100%)}
.brand{left:111px;top:20px;display:flex;align-items:center;gap:18px}
.brand-mark{width:64px;height:64px;background:var(--accent-dark)}
.brand-name{font:500 33px 'Roboto',sans-serif;color:var(--accent-dark);white-space:nowrap}
.nav{top:45px;font:500 13px 'Roboto',sans-serif;color:var(--ink);text-transform:uppercase}
.nav.active{color:var(--accent)}
.hero-title{left:0;width:1200px;text-align:center;color:var(--white);font-family:'Oswald',sans-serif;font-weight:600;font-size:36px;line-height:48px;top:249px;text-transform:uppercase}
.hero-sub{left:0;width:1200px;text-align:center;color:var(--white);font:500 23px 'Roboto',sans-serif;top:362px;text-transform:uppercase}

/* grid */
.frame{border:2px solid var(--navy)}
.role-list{left:664px;top:891px;list-style:none}
.role-list li{height:41px;display:flex;align-items:center;gap:22px;font-size:16px;color:var(--text);white-space:nowrap}
.role-list svg{flex:none}
.feature{top:1243px;width:245px;height:210px;display:flex;flex-direction:column;align-items:center;justify-content:flex-end;padding-bottom:48px;gap:28px;font:500 17px 'Roboto',sans-serif;color:var(--navy);text-transform:uppercase;white-space:nowrap}
.about-text{left:164px;top:1580px;width:388px;font-size:14.5px;line-height:25px;color:var(--text);text-align:justify}
.about-text p+p{margin-top:16px}

/* footer */
.footer{left:0;top:2772px;width:1200px;height:411px;background:var(--footer)}
.contact-icon{width:44px;height:44px;border:2px solid var(--white);border-radius:50%;display:flex;align-items:center;justify-content:center}
.contact-text{color:var(--white);font-size:14px;line-height:23px;white-space:nowrap}
.field{position:absolute;border:1px solid #c9d4e0;color:var(--white);font-size:13px;padding:14px 16px}
.foot-nav{left:965px;top:2835px;list-style:none}
.foot-nav li{color:var(--white);font:500 16px 'Roboto',sans-serif;height:31px;text-transform:uppercase}
</style>
</head>
<body>

<!-- hero -->
<div class="abs hero" role="img" aria-label="City skyline at sunset with a bay bridge and trees in the foreground"></div>
<div class="abs brand"><span class="brand-mark"></span><span class="brand-name">Okenta Holdings</span></div>
<span class="abs nav active" style="left:579px">Home</span>
<span class="abs nav" style="left:638px">About</span>
<span class="abs nav" style="left:702px">Strategy</span>
<span class="abs nav" style="left:788px">Projects</span>
<span class="abs nav" style="left:874px">Contact</span>
<div class="btn" style="left:965px;top:30px;width:123px;height:46px;font-size:13px">Get a Quote</div>
<h1 class="abs hero-title">Private Commercial<br>Real Estate Investment &amp; Development Firm</h1>
<p class="abs hero-sub">Building Together. Growing Together.</p>

<!-- role -->
<div class="abs frame" style="left:111px;top:774px;width:977px;height:471px"></div>
<div class="abs" style="left:113px;top:776px;width:486px;height:467px;background:linear-gradient(160deg,#d8d4cc,#a49b90 60%,#6f6862)" role="img" aria-label="Modern white kitchen with stainless appliances and pendant lights"></div>
<div class="abs" style="left:599px;top:774px;width:2px;height:471px;background:var(--navy)"></div>
<h2 class="abs heading" style="left:664px;top:826px;font-size:32px;line-height:44px">Role of Bramble Acres</h2>
<ul class="abs role-list">
  <li><svg width="15" height="15" viewBox="0 0 16 16"><circle cx="8" cy="8" r="8" fill="#3d6f9f"/><path d="M4 8h7M8 5l3 3-3 3" stroke="#fff" stroke-width="2" fill="none"/></svg>Opportunity Procurement</li>
  <li><svg width="15" height="15" viewBox="0 0 16 16"><circle cx="8" cy="8" r="8" fill="#3d6f9f"/><path d="M4 8h7M8 5l3 3-3 3" stroke="#fff" stroke-width="2" fill="none"/></svg>Development</li>
  <li><svg width="15" height="15" viewBox="0 0 16 16"><circle cx="8" cy="8" r="8" fill="#3d6f9f"/><path d="M4 8h7M8 5l3 3-3 3" stroke="#fff" stroke-width="2" fill="none"/></svg>Entitlements</li>
  <li><svg width="15" height="15" viewBox="0 0 16 16"><circle cx="8" cy="8" r="8" fill="#3d6f9f"/><path d="M4 8h7M8 5l3 3-3 3" stroke="#fff" stroke-width="2" fill="none"/></svg>Financial Underwriting</li>
  <li><svg width="15" height="15" viewBox="0 0 16 16"><circle cx="8" cy="8" r="8" fill="#3d6f9f"/><path d="M4 8h7M8 5l3 3-3 3" stroke="#fff" stroke-width="2" fill="none"/></svg>Capital Raising</li>
</ul>
<div class="btn" style="left:664px;top:1131px;width:129px;height:51px">More Info</div>

<!-- features -->
<div class="abs frame feature" style="left:111px">
  <svg width="64" height="64" viewBox="0 0 64 64" fill="none" stroke="#4b8fd0" stroke-width="3"><rect x="8" y="10" width="48" height="44" rx="3"/><text x="32" y="42" font-size="26" font-family="Roboto" fill="#4b8fd0" stroke="none" text-anchor="middle">$</text></svg>
  Investment Focus</div>
<div class="abs frame feature" style="left:355px">
  <svg width="64" height="64" viewBox="0 0 64 64" fill="none" stroke="#4b8fd0" stroke-width="3"><circle cx="32" cy="32" r="14"/><circle cx="32" cy="32" r="24" stroke-dasharray="8 6"/></svg>
  Development</div>
<div class="abs frame feature" style="left:599px">
  <svg width="64" height="64" viewBox="0 0 64 64" fill="none" stroke="#4b8fd0" stroke-width="3"><circle cx="32" cy="16" r="11"/><path d="M6 40l14-8 12 8 12-8 14 8M20 44l12 10 12-10"/></svg>
  Acquisitions</div>
<div class="abs frame feature" style="left:843px">
  <svg width="64" height="64" viewBox="0 0 64 64" fill="none" stroke="#4b8fd0" stroke-width="3"><rect x="8" y="24" width="22" height="32"/><rect x="30" y="14" width="26" height="42"/><path d="M14 32h10M14 42h10M36 24h14M36 34h14M36 44h14"/></svg>
  Product Types</div>

<!-- about -->
<div class="abs frame" style="left:111px;top:1451px;width:977px;height:472px"></div>
<div class="abs" style="left:599px;top:1451px;width:2px;height:472px;background:var(--navy)"></div>
<h2 class="abs heading" style="left:164px;top:1500px;font-size:42px;line-height:56px">About Us</h2>
<div class="abs about-text">
  <p>Okenta Holdings is a private real estate firm that specializes in the procurement, development, management, and disposition of various commercial real estate asset types including multifamily, industrial, single-family, hospitality, self-storage, and flex.</p>
  <p>The firm effectuates its strategy by utilizing long-standing relationships to ascertain acquisition and development opportunities within a specific target market. Bramble Acres is currently focused on acquisition and development opportunities in the southern portion of the United States.</p>
</div>
<div class="abs" style="left:601px;top:1453px;width:485px;height:468px;background:linear-gradient(170deg,#7a8fa6,#5c6e5a 55%,#3b4a58)" role="img" aria-label="Three partners standing outdoors in front of city towers"></div>

<!-- projects -->
<h2 class="abs heading" style="left:0;width:1200px;text-align:center;top:2022px;font-size:46px;line-height:62px">Recent Projects</h2>
<div class="abs" style="left:111px;top:2127px;width:205px;height:187px;background:linear-gradient(160deg,#2d3f6a,#556176 60%,#8a7a4c)" role="img" aria-label="Glass building terrace at dusk"></div>
<div class="abs" style="left:111px;top:2334px;width:205px;height:264px;background:linear-gradient(170deg,#b8c8dc,#6b5a4c 55%,#4c4440)" role="img" aria-label="Mid-rise mixed use apartment building"></div>
<div class="abs" style="left:337px;top:2127px;width:206px;height:266px;background:linear-gradient(180deg,#9ab8d8,#d4d3cd 50%,#8c6b50)" role="img" aria-label="White residential high-rise tower"></div>
<div class="abs" style="left:337px;top:2413px;width:206px;height:185px;background:linear-gradient(180deg,#1f4db0,#6a7aa0 50%,#b28a5a)" role="img" aria-label="Hotel facade lit at night"></div>
<div class="abs" style="left:566px;top:2127px;width:522px;height:471px;background:linear-gradient(170deg,#a9c2dc,#d9d3c8 45%,#8e8a86 80%,#7a7a70)" role="img" aria-label="Modern brick and stone townhomes with red doors"></div>
<div class="btn" style="left:535px;top:2642px;width:129px;height:50px">View All</div>

<!-- footer -->
<div class="abs footer"></div>
<div class="abs" style="left:1120px;top:2749px;width:44px;height:44px;border-radius:50%;background:var(--accent);display:flex;align-items:center;justify-content:center">
  <svg width="22" height="18" viewBox="0 0 22 18" fill="#fff"><ellipse cx="9" cy="7" rx="9" ry="6.5"/><ellipse cx="14" cy="11" rx="8" ry="5.5" opacity=".8"/></svg>
</div>
<h2 class="abs heading" style="left:111px;top:2824px;font-size:37px;line-height:50px;color:var(--white)">Contact Us</h2>

<div class="abs contact-icon" style="left:111px;top:2906px"><svg width="14" height="18" viewBox="0 0 14 18"><path d="M7 0a7 7 0 0 1 7 7c0 5-7 11-7 11S0 12 0 7a7 7 0 0 1 7-7z" fill="#fff"/><circle cx="7" cy="7" r="2.5" fill="#294a6b"/></svg></div>
<div class="abs contact-text" style="left:185px;top:2905px">Bramble Acres, PO Box<br>48120 Fairview, Texas 75001</div>
<div class="abs contact-icon" style="left:111px;top:2967px"><svg width="16" height="16" viewBox="0 0 16 16"><path d="M3 1l3 3-2 2c1 2 3 4 5 5l2-2 3 3-2 3C6 15 1 10 1 3z" fill="#fff"/></svg></div>
<div class="abs contact-text" style="left:185px;top:2978px">(555) 310-2276</div>
<div class="abs contact-icon" style="left:111px;top:3027px"><svg width="16" height="12" viewBox="0 0 16 12"><rect width="16" height="12" rx="1" fill="#fff"/><path d="M0 1l8 6 8-6" stroke="#294a6b" stroke-width="1.5" fill="none"/></svg></div>
<div class="abs contact-text" style="left:185px;top:3038px">info@brambleacres.com</div>

<div class="field" style="left:466px;top:2840px;width:188px;height:47px">First Name</div>
<div class="field" style="left:664px;top:2840px;width:188px;height:47px">Last Name</div>
<div class="field" style="left:466px;top:2898px;width:188px;height:47px">Phone</div>
<div class="field" style="left:664px;top:2898px;width:188px;height:47px">Address</div>
<div class="field" style="left:466px;top:2956px;width:386px;height:46px">Email</div>
<div class="field" style="left:466px;top:3013px;width:386px;height:74px">Type Your Message</div>
<div class="btn" style="left:466px;top:3098px;width:386px;height:46px">Submit</div>

<ul class="abs foot-nav">
  <li>Home</li><li>About</li><li>Strategy</li><li>Projects</li><li>Contact</li>
</ul>
<div class="btn" style="left:965px;top:3015px;width:123px;height:51px">Call Now</div>
<p class="abs contact-text" style="left:111px;top:3111px;font-size:13px">© 2022 Okenta Holdings</p>

</body>
</html>
```